NCBG website design

We need a page template website design for a cms website. Please see the brief attached for the details.
The client is the National Copperfleece Breeders Guild which is an organisation promoting the Copperfleece Sheep Breed within Australia.
Updates

Project Deadline Extended
Reason: So that my top few designs can make changes and re-submit.

Target Market(s)

See attached brief

```html
<!DOCTYPE html>
<html lang="en">
<head>
<meta charset="utf-8">
<title>National Copperfleece Breeders Guild</title>
<link href="https://fonts.googleapis.com/css2?family=Open+Sans:ital,wght@0,400;0,600;0,700;1,700&display=swap" rel="stylesheet">
<style>
:root{
  --green:#0b9444;
  --yellow:#ffd320;
  --dark:#222222;
  --dropdown:#2e2e2e;
  --text:#444444;
  --header-bg:#f6f6f6;
  --white:#ffffff;
}
*{box-sizing:border-box;margin:0;padding:0}
html,body{width:1029px;height:1200px;overflow:hidden;background:var(--white)}
body{position:relative;font-family:'Open Sans',sans-serif;color:var(--text)}

.site-header{position:absolute;left:0;top:0;width:1029px;height:98px;background:var(--header-bg)}
.brand{position:absolute;left:112px;top:28px;display:flex;align-items:center;gap:8px}
.brand-mark{width:22px;height:22px;border-radius:50%;background:var(--green)}
.brand-name{font-size:17px;font-weight:700;color:var(--green);line-height:1.1}
.site-title{position:absolute;left:271px;top:34px;font-size:17px;color:#444;font-weight:400}
.quick-tabs{position:absolute;top:68px;left:565px;display:flex;gap:3px}
.quick-tabs a{display:block;height:30px;line-height:30px;padding:0 5px;background:var(--green);color:var(--white);font-size:12.5px;font-weight:700;text-decoration:none;border-radius:3px 3px 0 0}

.main-nav{position:absolute;left:0;top:98px;width:1029px;height:50px;background:var(--dark)}
.main-nav a{position:absolute;top:0;height:50px;line-height:50px;color:var(--white);font-size:13.5px;text-decoration:none}
.main-nav a.active{background:var(--yellow);color:#333;text-align:center}
.main-nav a.active::after{content:"";position:absolute;left:50%;bottom:-6px;margin-left:-5px;border-left:5px solid transparent;border-right:5px solid transparent;border-top:6px solid var(--yellow)}
.dropdown{position:absolute;left:190px;top:148px;width:108px;height:58px;background:var(--dropdown);z-index:3;padding-top:10px}
.dropdown a{display:block;color:var(--white);font-size:12.5px;line-height:21px;padding-left:5px;text-decoration:none}

.hero{position:absolute;left:0;top:148px;width:1029px;height:345px;background:linear-gradient(180deg,#b8cde0 0%,#6f8a5a 30%,#4c6b35 52%,#7ea44c 70%,#8fb75a 100%)}
.hero-dots{position:absolute;left:490px;top:463px;display:flex;gap:6px}
.hero-dots span{width:12px;height:12px;border-radius:50%;background:#111}
.hero-dots span.on{background:var(--yellow)}

.intro{position:absolute;left:111px;top:522px;width:533px}
.intro h1{font-size:16.5px;font-weight:700;color:var(--green);margin-left:2px;margin-bottom:14px}
.intro h2{font-size:14px;font-weight:700;color:var(--green);margin:18px 0 10px}
.intro p{font-size:11.6px;line-height:20.6px;color:var(--text)}

.see-also{position:absolute;left:660px;top:510px;width:257px;height:318px;background:var(--green);border-radius:3px;color:var(--white);padding:12px 16px;font-size:12px;line-height:20.7px}
.see-also h3{font-size:12px;font-weight:700;margin-bottom:10px}
.see-also h4{font-size:12px;font-weight:700}
.see-also a{color:var(--white);font-weight:700;font-style:italic;text-decoration:none;display:block}
.see-also .gap{height:36px}

.sponsors{position:absolute;left:121px;top:876px;width:800px;height:82px}
.sponsors-label{position:absolute;left:0;top:24px;font-size:16px;font-weight:700;color:#444}
.sponsor{position:absolute;top:0;height:82px;display:flex;align-items:center;justify-content:center;font-size:13px;font-weight:700;text-align:center}
.s1{left:99px;width:112px;color:#00695c}
.s2{left:232px;width:89px;color:#fff;background:#00a99d}
.s3{left:340px;width:130px;color:#1e3c96}
.s4{left:477px;width:132px;color:#fff;background:#000}
.s5{left:620px;width:147px;color:#222;background:#ffe033}

.site-footer{position:absolute;left:0;top:978px;width:1029px;height:222px;background:var(--dark);color:var(--white)}
.footer-col{position:absolute;top:18px;list-style:none;font-size:12.3px;line-height:21.3px}
.footer-col.c1{left:115px;font-size:13px}
.footer-col.c2{left:289px}
.footer-col.c3{left:444px}
.contact{position:absolute;left:617px;top:18px;font-size:12.2px;line-height:24px}
.contact b{font-weight:700}
.follow{display:inline-block;margin-top:8px;width:86px;height:31px;background:var(--white);border-radius:2px;color:#333;font-size:11px;font-weight:600;line-height:31px;text-align:center}
.copyright{position:absolute;left:0;width:1029px;top:184px;text-align:center;font-size:12.2px}
.copyright b{color:var(--yellow)}
.copyright .studio{color:var(--green)}
</style>
</head>
<body>

<header class="site-header">
  <div class="brand"><span class="brand-mark"></span><span class="brand-name">Copperfleece</span></div>
  <div class="site-title">National Copperfleece Breeders Guild</div>
  <nav class="quick-tabs">
    <a href="#">Prime Lamb Helpline</a><a href="#">Events</a><a href="#">Members</a><a href="#">Latest News</a>
  </nav>
</header>

<nav class="main-nav">
  <a href="#" style="left:130px">Home</a>
  <a href="#" class="active" style="left:190px;width:64px">About</a>
  <a href="#" style="left:277px">Search</a>
  <a href="#" style="left:350px">Member Services</a>
  <a href="#" style="left:484px">Stud Pages</a>
  <a href="#" style="left:582px">News</a>
  <a href="#" style="left:647px">Sales</a>
  <a href="#" style="left:711px">Links</a>
  <a href="#" style="left:774px">Contact</a>
</nav>
<div class="dropdown">
  <a href="#">› Breed</a>
  <a href="#">› Genetic Testing</a>
</div>

<div class="hero" role="img" aria-label="Flock of pale sheep grazing on a green paddock below forested hills"></div>
<div class="hero-dots"><span class="on"></span><span></span><span></span></div>

<section class="intro">
  <h1>WELCOME TO COPPERFLEECE</h1>
  <p>The Copperfleece is an Australian breed developed for Australian conditions. The Copperfleece is proving to be the ideal prime lamb terminal sire in wide-ranging areas and environments of Australia.It is giving outstanding results in the dry, arid, pastoral zones; all types of agricultural, mixed farming areas; and also in higher rainfall districts.</p>
  <h2>THE NATIONAL COPPERFLEECE BREEDERS GUILD AIMS TO:</h2>
  <p>Be at the forefront of marketing and promotion of the Copperfleece breed &nbsp;&nbsp; better educate our members and commerical breeders on providing superior genetics to the Australian lamb industry continue to develop the Copperfleece breed to the advantage of all involved in the Australian lamb industry encourage extensive use of genetic evaluation and continue to benchmark the Copperfleece breed to become the leading performance breed remain at the forefront of recent technological advances within the livestock industry promote the Copperfleece as an alternative maternal sire</p>
</section>

<aside class="see-also">
  <h3>SEE ALSO :</h3>
  <h4>NATIONAL CONFERENCE 2014</h4>
  <div>Ashford, VIC</div>
  <div>Feb 16-19th</div>
  <div>Registration form now online</div>
  <div>Pen of 3 Rams Entry Form online</div>
  <a href="#" style="margin-top:4px">Click here To Know More &gt;&gt;</a>
  <div class="gap"></div>
  <h4>Millbrook Elite Sale 2013</h4>
  <div>Sunday 8th September at</div>
  <div>Millbrook Spring Show</div>
  <a href="#">Results &gt;&gt;</a>
</aside>

<section class="sponsors">
  <div class="sponsors-label">SPONSOR'S</div>
  <div class="sponsor s1">Fieldmark</div>
  <div class="sponsor s2">Veterra</div>
  <div class="sponsor s3">Ridgeway Haulage</div>
  <div class="sponsor s4">Southgate Bank</div>
  <div class="sponsor s5">Greenacre Seeds</div>
</section>

<footer class="site-footer">
  <ul class="footer-col c1"><li>Home</li><li>About</li><li>Testing</li><li>Search</li><li>Member Services</li></ul>
  <ul class="footer-col c2"><li>Stud Pages</li><li>News</li><li>Sales</li><li>Links</li><li>Contact</li></ul>
  <ul class="footer-col c3"><li>About the Breed</li><li>About the Association</li><li>Member Search</li><li>Stud Search</li></ul>
  <div class="contact">
    <div><b>Address</b> &nbsp;:PO Box 412, Millbrook, SA 5099</div>
    <div><b>Phone Work :</b> &nbsp;08 7000 1234</div>
    <div><b>Fax :</b> &nbsp;08 7000 5678</div>
    <div><b>Email :</b> &nbsp;info@copperfleece.org</div>
    <div class="follow">Follow us</div>
  </div>
  <div class="copyright">Copyright <b>National Copperfleece Breeders Guild</b> and Website design and development by &nbsp;<b class="studio">Lanternweb</b></div>
</footer>

</body>
</html>
```